FeedBack Solution Provider - Web Redesign

Lumetra Website design request We are looking for a redesign for our website www.lumetra-example.com 1 web page site +2, we are providing feedback collection solution through tablet devices and online iframes, sms, emails.. we want to optimize our website design to communicate our products values better (increase your customer satisfaction – get to know your customers – happy customers – increased business performance)Also to give visitors more insight to our different products (channels) layouts.A pricing section for minimum of 2 packages (SAAS) that include many features and hardware addons as a selection field. 3rd package clients to design their own packages through selection of components and addons no price needed in this feature (request quote).1 Web Page Sections will go as follows:1. Header2. Slider3. Why LumeTra (points and values)4. Features 5. Packages (pricing based on SaaS and hardware as addon)6. Impact of using RaiBack7. Clients Testimonies8. Contact9. Footer +2 Web Pages Adding to additional web pages by copying the following sections with different content (will be hidden for the moment)1. Slider2. Features 3. Packages (pricing based on SaaS and hardware as addon)4. Impact of using RaiBack5. Clients TestimoniesHints: https://pelvoran42.sitebuilder-example.com/lumetra www.lumetra-example.com

Target Market(s)

B2B

Industry/Entity Type

SaaS

Number of Pages Required

1 page

Font styles to use
Sans Serif

Colors

Designer to choose colors to be used in the design.

Requirements
Must have
• 1 Web Page Sections will go as follows:
• 1. Header
• 2. Slider
• 3. Why LumeTra (points and values)
• 4. Features
• 5. Packages (pricing based on SaaS and hardware as addon)
• 6. Impact of using LumeTra
• 7. Clients Testimonies
• 8. Contact
• 9. Footer
Nice to have
• +2 Web Pages Adding to additional web pages by copying the following sections with different content (will be hidden for the moment)
• 1. Slider
• 2. Features
• 3. Packages (pricing based on SaaS and hardware as addon)
• 4. Impact of using LumeTra
• 5. Clients Testimonies

```html
<!DOCTYPE html>
<html lang="en">
<head>
<meta charset="utf-8">
<title>Lumetra — Customer Feedback Solutions</title>
<link href="https://fonts.googleapis.com/css2?family=Lato:wght@400;700;900&family=Open+Sans:wght@400;600;700&display=swap" rel="stylesheet">
<style>
:root{
  --blue:#2b8fe6;
  --blue-dark:#1f6fc0;
  --orange:#f7921e;
  --ink:#1b1b1b;
  --text:#555;
  --muted:#8a8a8a;
  --light:#f3f4f6;
  --footer:#1e1e1e;
  --white:#fff;
}
*{box-sizing:border-box;margin:0;padding:0}
html,body{width:1200px;height:4932px;overflow:hidden}
body{position:relative;background:var(--white);font-family:"Open Sans",Arial,sans-serif;color:var(--text)}
.abs{position:absolute}
h2.section-title{position:absolute;left:0;width:1200px;text-align:center;font-family:"Lato",Arial,sans-serif;font-weight:900;font-size:44px;color:var(--ink);letter-spacing:1px}
.btn{position:absolute;display:flex;align-items:center;justify-content:center;gap:8px;border-radius:30px;font-family:"Lato",Arial,sans-serif;font-weight:700;font-size:14px;text-transform:uppercase}
.btn-orange{background:var(--orange);color:var(--white)}
.btn-ghost{border:2px solid var(--white);color:var(--white)}
.btn .dot{width:12px;height:12px;border-radius:50%;background:var(--white);display:inline-block}

/* header */
.site-header{position:absolute;top:0;left:0;width:1200px;height:138px;background:var(--white)}
.brand{position:absolute;display:flex;align-items:center;gap:10px;font-family:"Lato",Arial,sans-serif;font-weight:700;color:var(--blue)}
.brand .mark{border-radius:50%;border:3px solid var(--blue)}
.nav{position:absolute;top:58px;left:366px;display:flex;gap:34px;font-family:"Lato",Arial,sans-serif;font-weight:700;font-size:15px;color:var(--ink)}

/* hero */
.hero{position:absolute;top:138px;left:0;width:1200px;height:618px;overflow:hidden}
.hero-photo{position:absolute;inset:0;background:linear-gradient(100deg,#3a3430 0%,#5a5149 40%,#8a7d70 70%,#a49887 100%)}
.hero-title{position:absolute;left:112px;top:180px;font-family:"Lato",Arial,sans-serif;font-weight:900;font-size:64px;color:var(--white);letter-spacing:3px}
.hero-sub{position:absolute;left:112px;top:272px;width:470px;font-size:18px;line-height:30px;color:var(--white)}
.slider-arrow{position:absolute;width:30px;height:46px;background:var(--white);display:flex;align-items:center;justify-content:center}
.slider-arrow.blue{background:var(--blue)}

/* why */
.why-text{position:absolute;left:240px;top:972px;width:720px;text-align:center;font-size:14px;line-height:26px;color:var(--muted)}
.value{position:absolute;border-radius:50%;background:var(--white);box-shadow:0 6px 24px rgba(0,0,0,.12);display:flex;flex-direction:column;align-items:center;justify-content:center;text-align:center;font-family:"Lato",Arial,sans-serif;font-weight:700;font-size:18px;color:var(--ink);text-transform:uppercase;line-height:24px}
.value.active{background:var(--orange);color:var(--white);border:12px solid rgba(247,146,30,.35);background-clip:padding-box}
.round-arrow{position:absolute;width:44px;height:44px;border-radius:50%;display:flex;align-items:center;justify-content:center}

/* features */
.features{position:absolute;top:1529px;left:0;width:1200px;height:625px;background:linear-gradient(180deg,#eceef1 0%,#f6f7f8 60%,#ffffff 100%)}
.features-title{position:absolute;left:655px;top:166px;font-family:"Lato",Arial,sans-serif;font-weight:900;font-size:42px;color:var(--ink)}
.features-text{position:absolute;left:655px;top:245px;width:435px;font-size:14px;line-height:28px;color:var(--text)}

/* packages */
.plan{position:absolute;top:2367px;width:310px;height:434px;background:var(--white);box-shadow:0 4px 18px rgba(0,0,0,.12);text-align:center}
.plan-head{position:relative;height:96px;color:var(--white);font-family:"Lato",Arial,sans-serif;font-weight:900;font-size:22px;letter-spacing:1px}
.plan-head svg{position:absolute;inset:0}
.plan-head span{position:relative;top:22px}
.plan-label{margin-top:12px;font-size:14px;color:var(--muted)}
.plan-price{font-family:"Lato",Arial,sans-serif;font-weight:900;font-size:38px;color:var(--orange);line-height:46px}
.plan-comp{text-align:left;margin:22px 0 0 60px;font-family:"Lato",Arial,sans-serif;font-weight:700;font-size:17px;color:var(--ink)}
.plan ul{list-style:none;margin:10px 0 0 60px;width:220px;text-align:left;font-size:13px;line-height:25px;color:var(--text)}
.plan li{display:flex;justify-content:space-between}
.plan li::before{content:"›";color:var(--blue);margin-right:8px;font-weight:700}
.plan li b{margin-left:auto;font-weight:400}
.plan-btn{position:absolute;left:77px;bottom:42px;width:156px;height:34px;border-radius:20px;font-family:"Lato",Arial,sans-serif;font-weight:700;font-size:12px;display:flex;align-items:center;justify-content:center;text-transform:uppercase}
.plan-btn.outline{border:1.5px solid var(--orange);color:var(--orange)}
.plan-btn.filled{background:var(--blue);color:var(--white)}

/* impact */
.impact-title{position:absolute;left:110px;top:3030px;font-family:"Lato",Arial,sans-serif;font-weight:900;font-size:44px;line-height:54px;color:var(--ink)}
.impact-text{position:absolute;left:110px;top:3160px;width:495px;font-size:14px;line-height:27px;color:var(--text)}

/* testimonials */
.testi-card{position:absolute;top:3781px;width:305px;height:204px;background:var(--white);box-shadow:0 4px 16px rgba(0,0,0,.12);text-align:center;padding:58px 26px 0}
.testi-card .q{position:absolute;top:14px;left:0;width:100%;font-family:"Lato",Arial,sans-serif;font-weight:900;font-size:54px;line-height:54px;color:#c9c9c9}
.testi-card p{font-size:12px;line-height:20px;color:var(--text)}
.avatar{position:absolute;top:3945px;width:80px;height:80px;border-radius:50%;border:4px solid var(--white);background:linear-gradient(160deg,#8a95a0,#4d5864)}
.testi-name{position:absolute;top:4038px;width:305px;text-align:center;font-size:13px;color:var(--text)}
.testi-name b{font-family:"Lato",Arial,sans-serif;color:var(--ink)}

/* contact */
.contact{position:absolute;left:191px;top:4208px;width:818px;height:461px;background:var(--white);box-shadow:0 8px 30px rgba(0,0,0,.18)}
.contact-info{position:absolute;left:0;top:0;width:296px;height:461px;background:var(--orange);color:var(--white);padding:30px 30px}
.contact-info h3{font-family:"Lato",Arial,sans-serif;font-weight:700;font-size:22px;margin-bottom:34px}
.info-item{display:flex;gap:12px;margin-bottom:26px}
.info-item h4{font-family:"Lato",Arial,sans-serif;font-weight:700;font-size:18px;margin-bottom:6px}
.info-item p{font-size:12px;line-height:20px}
.socials{position:absolute;left:30px;bottom:28px;display:flex;gap:14px}
.socials span{width:14px;height:14px;border-radius:50%;background:var(--white);display:block}
.contact-form{position:absolute;left:336px;top:30px;width:445px}
.contact-form h3{font-family:"Lato",Arial,sans-serif;font-weight:700;font-size:22px;color:var(--ink);margin-bottom:22px}
.field{height:54px;border-bottom:1px solid #d6d6d6;font-size:13px;color:var(--text);padding-top:12px}
.field.tall{height:108px}
.captcha{position:absolute;left:0;top:362px;width:190px;height:52px;border:1px solid #d8d8d8;background:#f9f9f9;display:flex;align-items:center;gap:10px;padding-left:12px;font-size:11px;color:var(--text)}
.captcha i{width:20px;height:20px;border:2px solid #bdbdbd;background:var(--white);display:block}
.submit{position:absolute;right:0;top:364px;width:118px;height:44px;border-radius:24px;background:var(--blue);color:var(--white);font-family:"Lato",Arial,sans-serif;font-weight:700;font-size:16px;display:flex;align-items:center;justify-content:center}

/* footer */
.site-footer{position:absolute;top:4537px;left:0;width:1200px;height:395px;background:var(--footer)}
.footer-links{position:absolute;top:4830px;left:0;width:1200px;display:flex;justify-content:center;gap:18px;font-family:"Lato",Arial,sans-serif;font-weight:700;font-size:14px;color:var(--white)}
.footer-links i{font-style:normal;color:#888}
.copyright{position:absolute;top:4871px;left:0;width:1200px;text-align:center;font-size:13px;color:#cfcfcf}
</style>
</head>
<body>

<!-- Header -->
<header class="site-header">
  <div class="brand" style="left:110px;top:40px;font-size:26px">
    <span class="mark" style="width:40px;height:40px"></span>LumeTra
  </div>
  <nav class="nav">
    <span>HOME</span><span>ASK LUMETRA</span><span>OUR CLIENTS</span><span>CONTROL BOARD</span><span>ADVANTAGES</span><span>MORE ▾</span>
  </nav>
</header>

<!-- Slider -->
<section class="hero">
  <div class="hero-photo" role="img" aria-label="Photo of two café staff reviewing customer feedback on a tablet"></div>
  <h1 class="hero-title">LUMETRA</h1>
  <p class="hero-sub">LumeTra The first solution to measuring customer satisfaction in the Kingdom.</p>
  <div class="btn btn-orange" style="left:112px;top:366px;width:162px;height:44px">Read more <span class="dot"></span></div>
  <div class="btn btn-ghost" style="left:300px;top:366px;width:178px;height:44px">Get a quote <span class="dot"></span></div>
  <div class="slider-arrow" style="left:0;top:240px"><svg width="12" height="16"><path d="M9 2 3 8l6 6" stroke="#2b8fe6" stroke-width="2.5" fill="none"/></svg></div>
  <div class="slider-arrow blue" style="right:0;top:240px"><svg width="12" height="16"><path d="M3 2l6 6-6 6" stroke="#fff" stroke-width="2.5" fill="none"/></svg></div>
  <svg class="abs" style="left:0;bottom:0" width="1200" height="160" viewBox="0 0 1200 160">
    <path d="M0 20 Q600 200 1200 10 L1200 160 L0 160Z" fill="#fff"/>
    <path d="M0 40 Q600 205 1200 30" stroke="#2b8fe6" stroke-width="9" fill="none"/>
    <path d="M0 40 Q600 205 1200 30 L1200 160 L0 160Z" fill="#fff"/>
  </svg>
</section>

<!-- Why -->
<h2 class="section-title" style="top:884px">WHY LUMETRA?</h2>
<p class="why-text">Lorem ipsum dolor sit amet, consectetur adipiscing elit, sed do eiusmod tempor incididunt ut labore et dolore magna aliqua. Ut enim ad minim veniam, quis nostrud exercitation ullamco.</p>
<div class="round-arrow" style="left:34px;top:1220px;background:var(--white);box-shadow:0 2px 8px rgba(0,0,0,.15)"><svg width="12" height="16"><path d="M9 2 3 8l6 6" stroke="#2b8fe6" stroke-width="2.5" fill="none"/></svg></div>
<div class="round-arrow" style="left:1120px;top:1220px;background:var(--blue)"><svg width="12" height="16"><path d="M3 2l6 6-6 6" stroke="#fff" stroke-width="2.5" fill="none"/></svg></div>
<div class="value" style="left:132px;top:1115px;width:254px;height:254px">
  <svg width="84" height="70" viewBox="0 0 84 70"><g stroke="#2b8fe6" stroke-width="6" stroke-linecap="round"><path d="M16 4v62M42 4v62M68 4v62"/></g><g fill="#fff" stroke="#2b8fe6" stroke-width="5"><circle cx="16" cy="44" r="9"/><circle cx="42" cy="20" r="9"/><circle cx="68" cy="38" r="9"/></g></svg>
  <span style="margin-top:14px">Professional<br>control panel</span>
</div>
<div class="value active" style="left:436px;top:1073px;width:330px;height:330px">
  <svg width="80" height="66" viewBox="0 0 80 66"><rect x="4" y="4" width="72" height="44" rx="4" fill="none" stroke="#fff" stroke-width="6"/><path d="M30 62h20M40 48v14" stroke="#fff" stroke-width="6"/></svg>
  <span style="margin-top:16px">Consistency with identity<br>and devices</span>
  <svg style="margin-top:18px" width="24" height="24"><circle cx="12" cy="12" r="11" fill="#fff"/><path d="M12 6v12M6 12h12" stroke="#f7921e" stroke-width="3"/></svg>
</div>
<div class="value" style="left:812px;top:1115px;width:254px;height:254px">
  <svg width="70" height="76" viewBox="0 0 70 76"><rect x="10" y="6" width="48" height="62" rx="4" fill="none" stroke="#2b8fe6" stroke-width="6"/><path d="M20 26h28M20 38h28M20 50h16" stroke="#2b8fe6" stroke-width="5"/></svg>
  <span style="margin-top:14px">Evaluation and<br>comparison</span>
</div>

<!-- Features -->
<section class="features">
  <div class="abs" role="img" aria-label="Desktop monitor showing the satisfaction dashboard with pie and line charts" style="left:30px;top:150px;width:610px;height:330px;background:linear-gradient(160deg,#e6e9ee 0%,#ffffff 40%,#c9ced6 100%);border-radius:10px"></div>
  <h2 class="features-title">OUR FEATURES</h2>
  <p class="features-text">The Customer Satisfaction Assessment and Measurement System includes an easy and innovative mechanism for measuring the satisfaction of customers, employees or beneficiaries of the services and products provided by the customer choosing his or her satisfaction with the service by clicking on one of the following evaluation options.</p>
  <div class="btn btn-orange" style="left:655px;top:476px;width:172px;height:44px">Read more <span class="dot"></span></div>
</section>

<!-- Packages -->
<h2 class="section-title" style="top:2255px">OUR PACKAGES</h2>
<div class="plan" style="left:108px">
  <div class="plan-head"><svg width="310" height="96"><path d="M0 0H310V62L0 96Z" fill="#2b8fe6"/></svg><span>SILVER PLAN</span></div>
  <div class="plan-label">Price</div><div class="plan-price">$125</div>
  <div class="plan-comp">Components:</div>
  <ul><li>Excepteur sint<b>1</b></li><li>Nemo enim ipsum<b>3</b></li><li>Ut enim minima<b>4</b></li><li>Nor again is there<b>3</b></li></ul>
  <div class="plan-btn outline">Request a quote</div>
</div>
<div class="plan" style="left:447px">
  <div class="plan-head"><svg width="310" height="96"><path d="M0 0H310V62L0 96Z" fill="#f7921e"/></svg><span>GOLD PLAN</span></div>
  <div class="plan-label">Price</div><div class="plan-price">$325</div>
  <div class="plan-comp">Components:</div>
  <ul><li>Excepteur sint<b>2</b></li><li>Nemo enim ipsum<b>4</b></li><li>Ut enim minima<b>4</b></li><li>Nor again is there<b>3</b></li></ul>
  <div class="plan-btn filled">Request a quote</div>
</div>
<div class="plan" style="left:782px">
  <div class="plan-head"><svg width="310" height="96"><path d="M0 0H310V62L0 96Z" fill="#2b8fe6"/></svg><span>PLATINUM PLAN</span></div>
  <div class="plan-label">Price</div><div class="plan-price">$525</div>
  <div class="plan-comp">Components:</div>
  <ul><li>Excepteur sint<b>4</b></li><li>Nemo enim ipsum<b>4</b></li><li>Ut enim minima<b>6</b></li><li>Nor again is there<b>5</b></li></ul>
  <div class="plan-btn outline">Request a quote</div>
</div>
<div class="abs" style="left:108px;top:2926px;width:984px;height:1px;background:#d9d9d9"></div>

<!-- Impact -->
<h2 class="impact-title">IMPACT OF USING<br>LUMETRA</h2>
<p class="impact-text">Nemo enim ipsam voluptatem quia voluptas sit aspernatur aut odit aut fugit, sed quia consequuntur magni dolores eos qui ratione. Voluptatem sequi nesciunt neque porro quisquam est, qui dolorem ipsum quia dolor sit amet, consectetur, adipisci velit, sed quia non numquam eius modi tempora in cidunt ut labore et dolore magnam aliquam...</p>
<div class="btn btn-orange" style="left:112px;top:3338px;width:152px;height:40px">Read more <span class="dot"></span></div>
<div class="abs" role="img" aria-label="Photo of a hand holding a phone showing a rating screen" style="left:672px;top:3054px;width:432px;height:282px;background:linear-gradient(135deg,#5b4a3e 0%,#8c735f 45%,#c4b3a0 100%)"></div>
<svg class="abs" style="left:656px;top:3038px" width="464" height="314" viewBox="0 0 464 314" fill="none" stroke="#2b8fe6" stroke-width="5">
  <path d="M2 40V2H40M424 2H462V40M462 274V312H424M40 312H2V274"/>
</svg>

<!-- Testimonials -->
<svg class="abs" style="left:0;top:3460px" width="1200" height="420" viewBox="0 0 1200 420">
  <defs><linearGradient id="wave" x1="0" y1="0" x2="0" y2="1"><stop offset="0" stop-color="#2b8fe6"/><stop offset=".55" stop-color="#2b8fe6"/><stop offset="1" stop-color="#2b8fe6" stop-opacity="0"/></linearGradient></defs>
  <path d="M0 60 Q600 -40 1200 40 L1200 420 L0 420Z" fill="url(#wave)"/>
</svg>
<div class="abs" style="left:0;top:3840px;width:1200px;height:360px;background:linear-gradient(180deg,rgba(230,232,236,0) 0%,#eef0f3 40%,#f4f5f7 100%)"></div>
<h2 class="section-title" style="top:3663px;color:var(--white)">OUR TESTIMONIALS</h2>
<div class="round-arrow" style="left:30px;top:3862px;background:var(--white);box-shadow:0 2px 8px rgba(0,0,0,.15)"><svg width="12" height="16"><path d="M9 2 3 8l6 6" stroke="#f7921e" stroke-width="2.5" fill="none"/></svg></div>
<div class="round-arrow" style="left:1126px;top:3862px;background:var(--white);box-shadow:0 2px 8px rgba(0,0,0,.15)"><svg width="12" height="16"><path d="M3 2l6 6-6 6" stroke="#f7921e" stroke-width="2.5" fill="none"/></svg></div>

<div class="testi-card" style="left:108px"><div class="q">“</div><p>"At vero eos et accusamus et iusto odio dignissimos ducimus qui blanditiis tatum deleri anti atque corrupti quos dolores et quas ex illo gitur molestias"</p></div>
<div class="testi-card" style="left:450px"><div class="q" style="color:var(--orange)">“</div><p>"At vero eos et accusamus et iusto odio dignissimos ducimus qui blanditiis tatum deleri anti atque corrupti quos dolores et quas ex illo gitur molestias"</p></div>
<div class="testi-card" style="left:789px"><div class="q">“</div><p>"At vero eos et accusamus et iusto odio dignissimos ducimus qui blanditiis tatum deleri anti atque corrupti quos dolores et quas ex illo gitur molestias"</p></div>
<div class="avatar" role="img" aria-label="Portrait photo of client" style="left:220px"></div>
<div class="avatar" role="img" aria-label="Portrait photo of client" style="left:562px"></div>
<div class="avatar" role="img" aria-label="Portrait photo of client" style="left:901px"></div>
<div class="testi-name" style="left:108px"><b>DARREN VOSK,</b> Creative Manager</div>
<div class="testi-name" style="left:450px"><b>MIRA TALLEN,</b> Creative Manager</div>
<div class="testi-name" style="left:789px"><b>OWEN PERAL,</b> Creative Manager</div>

<!-- Footer -->
<footer class="site-footer"></footer>
<div class="brand" style="left:546px;top:4700px;font-size:26px">
  <span class="mark" style="width:34px;height:34px"></span>LumeTra
</div>
<div class="footer-links"><span>Terms</span><i>|</i><span>Site Map</span><i>|</i><span>Rating</span><i>|</i><span>FAQs</span><i>|</i><span>Legal Notice</span><i>|</i><span>Privacy Policy</span></div>
<div class="copyright">Copyrights © 2019 LumeTra. All Rights Reserved.</div>

<!-- Contact -->
<section class="contact">
  <div class="contact-info">
    <h3>Get In Touch</h3>
    <div class="info-item">
      <svg width="16" height="22" viewBox="0 0 16 22"><path d="M8 1a7 7 0 0 1 7 7c0 5-7 13-7 13S1 13 1 8a7 7 0 0 1 7-7z" fill="#fff"/><circle cx="8" cy="8" r="2.6" fill="#f7921e"/></svg>
      <div><h4>Address</h4><p>1200 Harbor Crest Road, North Quarter,<br>Sample City</p></div>
    </div>
    <div class="info-item">
      <svg width="16" height="18" viewBox="0 0 16 18"><path d="M3 1l3 4-2 2c1 3 3 5 6 6l2-2 4 3-2 3C7 17-1 9 1 3z" fill="#fff"/></svg>
      <div><h4>Phone Number</h4><p>800 555 0142</p></div>
    </div>
    <div class="info-item">
      <svg width="16" height="14" viewBox="0 0 16 14"><rect x="1" y="1" width="14" height="12" fill="#fff"/><path d="M1 1l7 6 7-6" stroke="#f7921e" stroke-width="1.5" fill="none"/></svg>
      <div><h4>Email</h4><p>info@lumetra-example.com</p></div>
    </div>
    <div class="socials"><span></span><span></span><span></span><span></span><span></span></div>
  </div>
  <div class="contact-form">
    <h3>Contact Us</h3>
    <div class="field">Your Name</div>
    <div class="field">Email Address</div>
    <div class="field">Phone Number</div>
    <div class="field tall">Message</div>
    <div class="captcha"><i></i>I'm not a robot</div>
    <div class="submit">SUBMIT</div>
  </div>
</section>

</body>
</html>
```